Velmor Spire Nine Flash website

we need a website to cater to 2 aspect of the business. We have Velmor spire residence and velmor spire office. For the office, we will get their inquire and arrange a face to face meetup to show them the office area for rent. For the residence side, it will need to be like staylane or roomvio.com. we want to allow them to book online for the date they need. We have a total of 10 different room configurations starting at $70 per night and up depending on the size of the room. example of the design is https://brisquelodge.com/

Target Market(s)

the website should have detail information on the layout, designs, and luxury of the building.

Industry/Entity Type

office and service appartment rental/lease

Coding

Coded - Design and coding required

Number of Pages Required

5+ page

Requirements
Must have
• a luxury perspective
Nice to have
• example https://brisquelodge.com/

```html
<!DOCTYPE html>
<html lang="en">
<head>
<meta charset="utf-8">
<title>Velmor Spire Nine — Landing Page Mobile View</title>
<link rel="stylesheet" href="https://fonts.googleapis.com/css2?family=Manrope:wght@400;500;600;700&display=swap">
<style>
  :root{
    --stage:#2c4d4b;
    --screen:#172c2c;
    --screen-soft:#1d3535;
    --panel:#566f6d;
    --gold:#d49a1f;
    --white:#ffffff;
    --muted:#b9c4c3;
    --line:#4b6361;
    --navy:#1b2340;
    --card-text:#6b7080;
    --light:#e3e6e5;
    --sky:#bfdcec;
    --sky-deep:#5e97b8;
    --room-warm:#c9a47c;
    --room-cool:#8d8f8c;
    --office-dark:#3c3a36;
    --office-light:#9a948a;
  }
  *{box-sizing:border-box;margin:0;padding:0}
  html,body{width:1200px;height:1200px;overflow:hidden}
  body{background:var(--stage);font-family:"Manrope",sans-serif;color:var(--white);position:relative}

  .wordmark{display:flex;align-items:center;gap:10px;font-family:"Manrope",sans-serif;font-weight:600;color:var(--gold);letter-spacing:0}
  .wordmark__box{border:1.5px solid var(--gold);flex:none}

  .intro{position:absolute;left:40px;top:90px;width:250px}
  .intro .wordmark{font-size:20px}
  .intro .wordmark__box{width:14px;height:14px}
  .intro__title{margin-top:22px;font-size:26px;font-weight:500;line-height:1.25}

  .screen{position:absolute;border-radius:18px;overflow:hidden;background:var(--screen)}
  .photo{display:block;width:100%}
  .photo--tower{background:linear-gradient(160deg,var(--sky) 0%,var(--sky-deep) 70%,#2d6c8e 100%)}
  .photo--office{background:linear-gradient(135deg,var(--office-light) 0%,var(--office-dark) 60%,#25231f 100%)}
  .photo--room{background:linear-gradient(135deg,var(--room-cool) 0%,#e9e2d6 45%,var(--room-warm) 100%)}

  .eyebrow{display:flex;align-items:center;gap:12px;font-size:11px;color:var(--muted);margin-bottom:10px}
  .eyebrow::before{content:"";width:30px;height:2px;background:var(--gold)}
  .headline{font-size:19px;font-weight:600;line-height:1.22}
  .headline em{font-style:normal;color:var(--gold)}
  .outline-btn{display:inline-block;border:1px solid var(--muted);color:var(--white);font-size:10px;padding:9px 16px;margin-top:16px}

  .hero{left:310px;top:50px;width:250px;height:710px}
  .hero__bar{display:flex;justify-content:space-between;align-items:center;padding:16px 16px 12px;border-bottom:1px solid var(--line)}
  .hero__bar .wordmark{font-size:9px;gap:6px}
  .hero__bar .wordmark__box{width:8px;height:8px;border-width:1px}
  .hero__menu{width:16px;height:10px;border-top:1.5px solid var(--gold);border-bottom:1.5px solid var(--gold)}
  .hero__body{padding:18px 16px}
  .hero__tag{font-size:12px;color:var(--white);padding-bottom:12px;border-bottom:1px solid var(--line)}
  .hero__title{font-size:22px;font-weight:600;color:var(--gold);line-height:1.2;margin-top:12px}
  .hero__text{font-size:9.5px;color:var(--muted);line-height:1.5;margin-top:10px}
  .hero__links{list-style:none;margin-top:20px}
  .hero__links li{display:flex;justify-content:space-between;align-items:center;font-size:11px;padding:11px 0;border-bottom:1px solid var(--line)}
  .hero__photo{position:absolute;left:0;bottom:0;height:190px}

  .office{left:590px;top:50px;width:250px;height:1110px}
  .office__photo{height:270px}
  .office__body{padding:22px 18px}
  .office__carousel{position:relative;margin:24px 18px 0;height:270px}
  .nav-dot{position:absolute;top:50%;width:20px;height:20px;margin-top:-10px;border-radius:50%;background:var(--white);display:flex;align-items:center;justify-content:center}
  .nav-dot--prev{left:-8px}.nav-dot--next{right:-8px}
  .office__teaser{position:absolute;left:0;right:0;bottom:0;height:150px;background:var(--panel);padding:22px 18px}

  .residence{left:40px;top:380px;width:240px;height:780px;background:var(--panel);padding:24px 16px}
  .room-card{background:var(--white);border-radius:10px;overflow:hidden;color:var(--navy);position:relative}
  .room-card__img{height:180px}
  .residence .room-card{margin-top:26px}
  .badge{position:absolute;left:10px;display:flex;align-items:center;gap:4px;background:var(--gold);color:var(--white);font-size:8px;font-weight:700;padding:4px 8px;border-radius:10px}
  .room-card__info{padding:12px 12px 14px}
  .price{font-size:15px;font-weight:700;color:var(--gold)}
  .price small{font-size:9px;font-weight:500;color:var(--card-text)}
  .room-card__name{font-size:15px;font-weight:700;margin-top:4px}
  .room-card__addr{font-size:9px;color:var(--card-text);margin-top:4px}
  .features{display:flex;gap:10px;font-size:8.5px;color:var(--card-text);margin-top:10px;padding-top:8px;border-top:1px solid #e7e7ea}
  .features span{display:flex;align-items:center;gap:3px}
  .heart{position:absolute;right:12px;width:26px;height:26px;border-radius:50%;border:1px solid #e3e3e8;display:flex;align-items:center;justify-content:center}
  .book-btn{display:block;text-align:center;border:1px solid var(--gold);color:var(--gold);font-size:10px;font-weight:600;border-radius:6px;padding:8px;margin-top:12px}

  .rooms{left:310px;top:790px;width:250px;height:370px;background:var(--screen-soft);padding:16px}
  .rooms .room-card__img{height:140px}

  .footer{left:870px;top:50px;width:290px;height:520px;padding:26px 20px}
  .footer .wordmark{font-size:19px}
  .footer .wordmark__box{width:14px;height:14px}
  .footer h3{font-size:13px;font-weight:700;margin-top:24px}
  .contact{list-style:none;margin-top:12px}
  .contact li{display:flex;align-items:center;gap:10px;font-size:10px;color:var(--muted);margin-bottom:10px}
  .subscribe{display:flex;margin-top:14px;height:38px}
  .subscribe__field{flex:1;background:var(--white);color:#8a8f97;font-size:10px;display:flex;align-items:center;padding-left:12px}
  .subscribe__send{width:44px;background:var(--gold);display:flex;align-items:center;justify-content:center}
  .consent{display:flex;align-items:center;gap:8px;font-size:9px;color:var(--muted);margin-top:10px}
  .consent span{width:13px;height:13px;border-radius:3px;background:var(--white);display:flex;align-items:center;justify-content:center}
  .social{display:flex;gap:14px;margin-top:22px;padding-bottom:16px;border-bottom:1px solid var(--line)}
  .social span{width:16px;height:16px;border-radius:50%;border:1.5px solid var(--muted)}
  .copyright{font-size:9.5px;color:var(--muted);margin-top:14px}

  .reviews{left:870px;top:600px;width:290px;height:560px;background:var(--light);color:var(--navy);padding:24px 18px}
  .reviews__title{font-size:20px;font-weight:700;line-height:1.2}
  .review{background:var(--white);border-radius:10px;padding:14px;margin-top:14px;display:flex;gap:10px}
  .review__avatar{width:30px;height:30px;border-radius:50%;background:#8a7b6e;flex:none}
  .review__quote{font-size:9.5px;line-height:1.5;color:#3a3f4c}
  .review__name{font-size:9px;color:var(--card-text);margin-top:6px}
  .reviews__next{font-size:17px;font-weight:700;margin-top:22px}
</style>
</head>
<body>

<header class="intro">
  <div class="wordmark"><span class="wordmark__box"></span>Velmor Spire Nine</div>
  <p class="intro__title">Landing Page<br>Mobile view</p>
</header>

<section class="screen residence">
  <div class="eyebrow">Residence</div>
  <h2 class="headline">Lease Your Dream Home at Velmor Spire Residence – <em>Where Luxury Meets Comfort</em></h2>
  <span class="outline-btn">Browse more rooms</span>
  <article class="room-card">
    <div class="photo photo--room room-card__img" role="img" aria-label="Photo of a standard hotel bedroom with bed and lamps"></div>
    <span class="badge" style="top:166px">✦ POPULAR</span>
    <div class="room-card__info">
      <span class="heart" style="top:204px"><svg width="12" height="12" viewBox="0 0 24 24" fill="none" stroke="#d49a1f" stroke-width="2"><path d="M12 21s-8-5-8-11a4.5 4.5 0 0 1 8-2.8A4.5 4.5 0 0 1 20 10c0 6-8 11-8 11z"/></svg></span>
      <div class="price">$70 <small>/day</small></div>
      <div class="room-card__name">Standart Room</div>
      <div class="room-card__addr">118 Harbor Crest, Lakeview Bay</div>
      <div class="features"><span>▭ 1 Beds</span><span>◡ 1 Bathrooms</span><span>▢ 3x3m²</span></div>
    </div>
  </article>
</section>

<section class="screen hero">
  <div class="hero__bar">
    <div class="wordmark"><span class="wordmark__box"></span>Velmor Spire Nine</div>
    <div class="hero__menu"></div>
  </div>
  <div class="hero__body">
    <p class="hero__tag">Discover Elevated Living and Working</p>
    <h1 class="hero__title">Velmor Spire Residence &amp; Office</h1>
    <p class="hero__text">Where Your Lifestyle Meets Your Professional Ambitions. Inquire Today and Let Us Guide You to Your Ideal Workspace</p>
    <span class="outline-btn">Get in touch</span>
    <ul class="hero__links">
      <li>Why Us <span>›</span></li>
      <li>Benefits <span>›</span></li>
      <li>View our location <span>›</span></li>
    </ul>
  </div>
  <div class="photo photo--tower hero__photo" role="img" aria-label="Photo of the tower's spire against a blue sky"></div>
</section>

<section class="screen rooms">
  <article class="room-card">
    <div class="photo photo--room room-card__img" role="img" aria-label="Photo of a standard hotel bedroom"></div>
    <span class="badge" style="top:128px">✦ POPULAR</span>
    <div class="room-card__info">
      <span class="heart" style="top:164px"><svg width="12" height="12" viewBox="0 0 24 24" fill="none" stroke="#d49a1f" stroke-width="2"><path d="M12 21s-8-5-8-11a4.5 4.5 0 0 1 8-2.8A4.5 4.5 0 0 1 20 10c0 6-8 11-8 11z"/></svg></span>
      <div class="price">$70 <small>/day</small></div>
      <div class="room-card__name">Standart Room</div>
      <div class="room-card__addr">118 Harbor Crest, Lakeview Bay</div>
      <div class="features"><span>▭ 1 Beds</span><span>◡ 1 Bathrooms</span><span>▢ 3x3m²</span></div>
      <span class="book-btn">Book Now</span>
    </div>
  </article>
</section>

<section class="screen office">
  <div class="photo photo--tower office__photo" role="img" aria-label="Photo of the glass tower with its pointed spire"></div>
  <div class="office__body">
    <div class="eyebrow">Office</div>
    <h2 class="headline" style="font-size:21px">Lease Your Office Space at Velmor Spire Office, <em>Where Innovation Meets Prestige</em></h2>
    <span class="outline-btn">Schedule your visit</span>
  </div>
  <div class="office__carousel">
    <div class="photo photo--office" style="height:100%" role="img" aria-label="Photo of an open office floor with glass walls and a meeting table"></div>
    <span class="nav-dot nav-dot--prev"><svg width="8" height="8" viewBox="0 0 10 10"><path d="M6.5 1.5 3 5l3.5 3.5" fill="none" stroke="#5b3fa0" stroke-width="1.6"/></svg></span>
    <span class="nav-dot nav-dot--next"><svg width="8" height="8" viewBox="0 0 10 10"><path d="M3.5 1.5 7 5 3.5 8.5" fill="none" stroke="#5b3fa0" stroke-width="1.6"/></svg></span>
  </div>
  <div class="office__teaser">
    <div class="eyebrow">Residence</div>
    <h2 class="headline">Lease Your Dream Home at Velmor Spire Residence</h2>
  </div>
</section>

<section class="screen footer">
  <div class="wordmark"><span class="wordmark__box"></span>Velmor Spire Nine</div>
  <h3>Information</h3>
  <ul class="contact">
    <li><svg width="12" height="12" viewBox="0 0 24 24" fill="none" stroke="#b9c4c3" stroke-width="2"><path d="M5 3h4l2 5-3 2a11 11 0 0 0 6 6l2-3 5 2v4a2 2 0 0 1-2 2A17 17 0 0 1 3 5a2 2 0 0 1 2-2z"/></svg>+1 (555) 014 - 2290</li>
    <li><svg width="12" height="12" viewBox="0 0 24 24" fill="none" stroke="#b9c4c3" stroke-width="2"><rect x="3" y="5" width="18" height="14"/><path d="m3 6 9 7 9-7"/></svg>hello@velmorspire.com</li>
    <li><svg width="12" height="12" viewBox="0 0 24 24" fill="none" stroke="#b9c4c3" stroke-width="2"><path d="M12 22s7-7 7-12a7 7 0 0 0-14 0c0 5 7 12 7 12z"/><circle cx="12" cy="10" r="2.5"/></svg>All Around The Globe</li>
  </ul>
  <h3>Subscribe Now</h3>
  <div class="subscribe">
    <div class="subscribe__field">Send Us A Message</div>
    <div class="subscribe__send"><svg width="16" height="16" viewBox="0 0 24 24" fill="#fff"><path d="M2 11 22 3l-8 20-3-9z"/></svg></div>
  </div>
  <div class="consent"><span><svg width="9" height="9" viewBox="0 0 10 10"><path d="m1.5 5 2.5 2.5L8.5 2" fill="none" stroke="#d49a1f" stroke-width="1.6"/></svg></span>By Signing Up, You Agree To Receive Mail.</div>
  <div class="social"><span></span><span></span><span></span></div>
  <p class="copyright">© 2023 Velmor Spire Nine. All Rights Reserved.</p>
</section>

<section class="screen reviews">
  <h2 class="reviews__title">Discover Residents &amp; Professionals at Velmor Spire: Real Satisfaction</h2>
  <article class="review">
    <div class="review__avatar" role="img" aria-label="Guest portrait"></div>
    <div>
      <p class="review__quote">"OMG! I cannot believe how easy this new landing page was to edit and publish for our team."</p>
      <p class="review__name">Noel Brandt</p>
    </div>
  </article>
  <article class="review">
    <div class="review__avatar" style="background:#5f8fa0" role="img" aria-label="Guest portrait"></div>
    <div>
      <p class="review__quote">"Simply the best. Better than all the rest. I'd recommend this place to beginners and advanced users who want success."</p>
      <p class="review__name">Owen Marsh</p>
    </div>
  </article>
  <p class="reviews__next">Experience Elevated</p>
</section>

</body>
</html>
```